Fresh, modern, fun business card for pediatric dental practice

Need a business card for fresh, modern, fun pediatric dental practice

Clean look that matches our website's font and colors

We prefer the look of curved corners on business cards

Target Market(s)

parents (mothers) of young children, professionals, mid-high class

Industry/Entity Type

Dental

Contact Information for Business Card

Maplebrook Pediatric Dentistry
482 Quarry Lane
Suite 517
Carrowfield, PA 17000
717.555.0193
www.maplebrookkidsdental.example

Mei-Ran Tsai, DMD
Corinne Walbeck, DMD
(we are working on our email address, but we would like that on the card as well)

Font styles to use
Sans Serif

Requirements
Must have
• All info; we would also like to make cards for individual staff members
• colors from our website and color palatte, attatched
• use same font and design as website for branding
Nice to have
• clean, simple card that has a pop of color
• we would like to see a few designs with our tag line "where smiles get brighter"
• we are not sure if we want to have it on there or not
• we would like to see a few designs incorporating the ribbon graphic on our website where the word WELCOME is

```html
<!DOCTYPE html>
<html lang="en">
<head>
<meta charset="utf-8">
<title>Maplebrook Pediatric Dentistry – Business Card</title>
<link rel="stylesheet" href="https://fonts.googleapis.com/css2?family=Ubuntu:wght@500&family=Roboto+Condensed:wght@600&family=Roboto:wght@400&display=swap">
<style>
  :root {
    --backdrop: #2a2a2a;
    --card-white: #f6f6f4;
    --brand-gold: #efb320;
    --card-gold: #eeb424;
    --ink: #464646;
    --white: #ffffff;
  }
  * { margin: 0; padding: 0; box-sizing: border-box; }
  html, body { width: 1200px; height: 960px; overflow: hidden; }
  body { background: var(--backdrop); position: relative; font-family: "Roboto", Arial, sans-serif; }

  .card {
    position: absolute;
    width: 600px;
    height: 343px;
    border-radius: 22px;
    box-shadow: 0 3px 8px rgba(0,0,0,0.45);
    overflow: hidden;
  }
  .card--front { left: 314px; top: 113px; background: var(--card-white); }
  .card--back { left: 311px; top: 472px; background: var(--card-gold); }

  /* brand lockup */
  .brand { position: absolute; font-family: "Ubuntu", Arial, sans-serif; font-weight: 500; line-height: 1; }
  .brand__dot { position: absolute; border-radius: 50%; }
  .brand__name { position: absolute; white-space: nowrap; letter-spacing: 0.5px; }
  .brand__tag { position: absolute; white-space: nowrap; letter-spacing: 0.6px; }

  .card--front .brand { color: var(--brand-gold); }
  .card--front .brand__dot { left: 103px; top: 30px; width: 40px; height: 40px; border: 3px solid var(--brand-gold); }
  .card--front .brand__name { left: 36px; top: 96px; font-size: 40px; }
  .card--front .brand__tag { left: 38px; top: 137px; font-size: 20px; }

  .doctors {
    position: absolute; right: 40px; top: 104px; text-align: right;
    font-family: "Roboto Condensed", "Arial Narrow", sans-serif; font-weight: 600;
    font-size: 21px; line-height: 24px; color: var(--brand-gold);
  }
  .divider { position: absolute; left: 36px; right: 40px; top: 166px; height: 1px; background: var(--brand-gold); }

  .contact { position: absolute; left: 36px; font-size: 14.5px; line-height: 18px; color: var(--ink); }
  .contact__row { position: relative; padding-left: 25px; }
  .contact__row svg { position: absolute; left: 0; top: 2px; width: 14px; height: 14px; }
  .contact--address { top: 191px; }
  .contact--reach { top: 275px; }

  .card--back .brand { color: var(--white); left: 0; width: 100%; text-align: center; }
  .card--back .brand__dot { left: 274px; top: 94px; width: 52px; height: 52px; border: 3px solid var(--white); }
  .card--back .brand__name { left: 0; width: 100%; top: 168px; font-size: 44px; }
  .card--back .brand__tag { left: 0; width: 100%; top: 215px; font-size: 23px; }
  .card--back .web {
    position: absolute; left: 0; width: 100%; top: 295px; text-align: center;
    color: var(--white); font-size: 13px; letter-spacing: 3.2px;
  }
</style>
</head>
<body>

  <section class="card card--front" aria-label="Business card front">
    <div class="brand">
      <span class="brand__dot"></span>
      <span class="brand__name">maplebrook</span>
      <span class="brand__tag">pediatric dentistry</span>
    </div>

    <div class="doctors">
      <p>Mei-Ran Tsai, DMD</p>
      <p>Corinne Walbeck, DMD</p>
    </div>

    <div class="divider"></div>

    <div class="contact contact--address">
      <div class="contact__row">
        <svg viewBox="0 0 14 14" aria-hidden="true"><path d="M7 0.5a4.6 4.6 0 0 0-4.6 4.6C2.4 8.4 7 13.5 7 13.5s4.6-5.1 4.6-8.4A4.6 4.6 0 0 0 7 0.5zm0 6.3a1.8 1.8 0 1 1 0-3.6 1.8 1.8 0 0 1 0 3.6z" fill="var(--brand-gold)"/></svg>
        <p>Maplebrook Pediatric Dentistry</p>
        <p>482 Quarry Lane</p>
        <p>Suite 517</p>
        <p>Carrowfield, PA 17000</p>
      </div>
    </div>

    <div class="contact contact--reach">
      <div class="contact__row">
        <svg viewBox="0 0 14 14" aria-hidden="true"><path d="M3 1l2.3 2.6-1.2 1.6c.8 1.8 2.3 3.3 4.1 4.1l1.6-1.2L12.4 10.4 11 12.6C6 12.3 1.7 8 1.4 3z" fill="var(--brand-gold)"/></svg>
        <p>717.555.0193</p>
      </div>
      <div class="contact__row">
        <svg viewBox="0 0 14 14" aria-hidden="true"><circle cx="7" cy="7" r="6.2" fill="var(--brand-gold)"/><path d="M4 4.5c1.2.2 1.8 1 1.5 2-.3.9.6 1.5 1.3 1.8.5.2.4 1.4-.2 2.4M9 2.2c-.5 1 .2 1.8 1.2 1.9.9.1 1.6.8 1.8 1.6" stroke="var(--card-white)" stroke-width="1.1" fill="none"/></svg>
        <p>maplebrookkidsdental.example</p>
      </div>
    </div>
  </section>

  <section class="card card--back" aria-label="Business card back">
    <div class="brand">
      <span class="brand__dot"></span>
      <span class="brand__name">maplebrook</span>
      <span class="brand__tag">pediatric dentistry</span>
    </div>
    <p class="web">www.maplebrookkidsdental.example</p>
  </section>

</body>
</html>
```